Brellwick Partners, LLC Stationary

Brellwick Partners, LLC is a new financial planning and consulting company. We are looking for designs on business cards, letterhead, envelopes, and anything else that would be useful. Our preference for business card design is two sided. We are looking for a professional and clean look with incorporating the logo and patriotic feel. Thank you to all who participate and good luck!

```html
<!DOCTYPE html>
<html lang="en">
<head>
<meta charset="utf-8">
<title>Brellwick Partners, LLC — Business Card</title>
<link rel="stylesheet" href="https://fonts.googleapis.com/css2?family=Raleway:wght@400;500;600;700&display=swap">
<style>
  :root {
    --navy: #1c4170;
    --red: #c8202f;
    --white: #ffffff;
    --ink: #4a4f57;
    --page: #e9eaec;
  }
  * { margin: 0; padding: 0; box-sizing: border-box; }
  html, body { width: 1200px; height: 950px; overflow: hidden; }
  body {
    background: var(--page);
    font-family: "Raleway", Arial, sans-serif;
    position: relative;
  }
  .card {
    position: absolute;
    left: 250px;
    width: 700px;
    height: 400px;
    border-radius: 22px;
    overflow: hidden;
    box-shadow: 0 10px 28px rgba(0,0,0,0.18);
  }
  .card-front { top: 40px; background: var(--white); }
  .card-back { top: 510px; background: var(--navy); }

  .front-wave { position: absolute; left: 0; top: 0; width: 700px; height: 400px; }

  .brand { position: absolute; left: 60px; top: 40px; display: flex; align-items: flex-start; gap: 14px; }
  .brand-mark { width: 18px; height: 18px; background: var(--red); flex: none; margin-top: 8px; }
  .brand-name {
    width: 240px;
    font-size: 30px; line-height: 1.1; font-weight: 700;
    color: var(--navy); letter-spacing: 0.5px;
  }
  .brand-tagline {
    position: absolute; left: 92px; top: 116px;
    font-size: 10px; font-weight: 600; letter-spacing: 1.4px;
    text-transform: uppercase; color: var(--red);
  }

  .divider { position: absolute; left: 400px; top: 50px; width: 1.5px; height: 150px; background: var(--red); opacity: 0.7; }

  .address {
    position: absolute; left: 430px; top: 60px;
    font-size: 17px; line-height: 1.5; color: var(--ink);
  }

  .person { position: absolute; left: 60px; top: 158px; }
  .person-name { font-size: 22px; font-weight: 700; color: var(--navy); letter-spacing: 1px; text-transform: uppercase; }
  .person-role { font-size: 18px; font-weight: 500; color: var(--red); letter-spacing: 0.5px; text-transform: uppercase; margin-top: 2px; }
  .contact-list { list-style: none; margin-top: 10px; }
  .contact-list li { display: flex; align-items: center; gap: 10px; font-size: 15px; color: var(--ink); line-height: 1.55; }
  .contact-icon { width: 14px; height: 14px; fill: var(--navy); flex: none; }

  .front-web {
    position: absolute; right: 46px; bottom: 34px;
    font-size: 16px; font-weight: 500; letter-spacing: 3px; color: var(--white);
  }

  .back-brand {
    position: absolute; left: 0; right: 0; top: 158px;
    display: flex; align-items: center; justify-content: center; gap: 16px;
  }
  .back-brand .brand-mark { width: 24px; height: 24px; margin-top: 0; }
  .back-brand-name { font-size: 44px; font-weight: 700; color: var(--white); letter-spacing: 1px; }
  .back-web {
    position: absolute; left: 0; right: 0; bottom: 60px; text-align: center;
    font-size: 16px; font-weight: 500; letter-spacing: 4px; color: var(--white);
  }
</style>
</head>
<body>

<section class="card card-front">
  <svg class="front-wave" viewBox="0 0 700 400" aria-hidden="true">
    <path d="M0 350 C 220 380, 420 330, 700 230 L700 400 L0 400 Z" fill="var(--red)"/>
    <path d="M0 362 C 230 392, 430 345, 700 248 L700 400 L0 400 Z" fill="var(--white)"/>
    <path d="M0 370 C 240 398, 440 358, 700 262 L700 400 L0 400 Z" fill="var(--navy)"/>
    <path d="M0 338 C 210 366, 410 318, 700 212" fill="none" stroke="var(--navy)" stroke-width="3"/>
    <path d="M0 330 C 200 356, 400 310, 700 200" fill="none" stroke="var(--red)" stroke-width="1.2"/>
  </svg>

  <div class="brand">
    <span class="brand-mark"></span>
    <span class="brand-name">Brellwick Partners, LLC</span>
  </div>
  <p class="brand-tagline">Financial Planning and Consulting</p>

  <div class="divider"></div>
  <p class="address">4120 Linden Court<br>Boise, Idaho 83702</p>

  <div class="person">
    <p class="person-name">Daniel Harlow</p>
    <p class="person-role">CEO/Founder</p>
    <ul class="contact-list">
      <li>
        <svg class="contact-icon" viewBox="0 0 24 24"><path d="M6.6 10.8a15.1 15.1 0 0 0 6.6 6.6l2.2-2.2a1 1 0 0 1 1-.25 11.4 11.4 0 0 0 3.6.57 1 1 0 0 1 1 1V20a1 1 0 0 1-1 1A17 17 0 0 1 3 4a1 1 0 0 1 1-1h3.5a1 1 0 0 1 1 1c0 1.25.2 2.45.57 3.57a1 1 0 0 1-.25 1z"/></svg>
        512 304 7719
      </li>
      <li>
        <svg class="contact-icon" viewBox="0 0 24 24"><path d="M6 2h12a1 1 0 0 1 1 1v18a1 1 0 0 1-1 1H6a1 1 0 0 1-1-1V3a1 1 0 0 1 1-1zm1 3v12h10V5z"/></svg>
        512 866 2041
      </li>
      <li>
        <svg class="contact-icon" viewBox="0 0 24 24"><path d="M2 5h20v14H2zm2 2v.5l8 5 8-5V7zm0 2.9V17h16V9.9l-8 5z"/></svg>
        hello@brellwick.com
      </li>
    </ul>
  </div>

  <p class="front-web">www.brellwick.com</p>
</section>

<section class="card card-back">
  <div class="back-brand">
    <span class="brand-mark"></span>
    <span class="back-brand-name">Brellwick Partners, LLC</span>
  </div>
  <p class="back-web">www.brellwick.com</p>
</section>

</body>
</html>
```